Ridge Lass Crew (Flyer)

I want a flyer to advertise my service.
Details below, and logo's to use are attached.

A girls only after school program, 11-14yrs, as OSHC is no longer avail, dedicated to coaching & mentoring our girls into strong, independent young women.

The Brainchild of Rebecca Folwin, Ridge Lass Crew was created to address the growing demand for after school/school holiday supervision for kids moving from primary into high school, when OSHC ceases to exist.
With over 12 years experience mentoring and coaching young women in the corporate world, Bec decided to leave her role as a Director with Tarrant Trust, and follow her passion.
Bec, along with her sister Lorraine, who has over 10 years experience in local communities as a Youth Worker, and is also a qualified Enrolled Nurse, embarked on building a program designed to keep parents happy (by knowing their girls are safe) and dedicated to coaching and mentoring our girls into strong, independent young women.
Open every afternoon and during school holidays, we look to offer;
- Daily meditation
- Healthy snacks
- Dedicated homework time
- Organised group activity, led by qualified instructors (yoga, fitness class, soccer etc)
- Regular guests speakers, addressing issues/concerns for young people today
- SOCIAL MEDIA FREE ZONE

Located 87 Pelham Pde, Baulkham Hills (across from Crestmoor Day Clinic)
Open 3-6pm Monday to Friday

Facebook page: http://fb.example/ridgelasscrew
Email: info@ridgelasscrew.example.au
Mobile: 0455817396

Target Market(s)

Parents of teenage girls, teenage girls 11-14 years

Industry/Entity Type

School

Font styles to use
Sans Serif

Colors
b768aa
e667a6

Requirements
Must have
• What progam is - see brief
• Who runs it
Should not have
• Not be too busy, not overly mature images

```html
<!DOCTYPE html>
<html lang="en">
<head>
<meta charset="utf-8">
<title>Ridge Lass Crew – After School Program Flyer</title>
<link href="https://fonts.googleapis.com/css2?family=Bebas+Neue&family=Oswald:wght@400;500&family=Kaushan+Script&family=Roboto:wght@700&display=swap" rel="stylesheet">
<style>
  :root {
    --purple: #a552f2;
    --purple-light: #c28cf6;
    --pink: #e667a6;
    --pink-soft: #f6c9f0;
    --ink: #1d1324;
    --white: #ffffff;
    --photo-light: #eeeef0;
    --photo-mid: #d9d8dc;
    --photo-skin: #e6c9b8;
  }
  html, body { margin: 0; padding: 0; overflow: hidden; background: #fff; }
  .flyer {
    position: relative;
    width: 861px;
    height: 1200px;
    overflow: hidden;
    font-family: "Bebas Neue", "Oswald", sans-serif;
    color: var(--ink);
  }
  .backdrop { position: absolute; inset: 0; }
  .abs { position: absolute; margin: 0; white-space: nowrap; }

  .logo-box {
    position: absolute; left: 30px; top: 56px; width: 335px; height: 382px;
    background: var(--white);
    display: flex; align-items: center; justify-content: center;
  }
  .logo-name {
    font-family: "Bebas Neue", sans-serif;
    font-size: 60px; line-height: 1; color: var(--pink);
    text-align: center; letter-spacing: 1px;
  }

  .headline {
    font-family: "Bebas Neue", sans-serif;
    color: var(--white);
    line-height: 1;
    text-shadow: -4px 3px 5px rgba(40, 20, 60, 0.45);
  }
  .headline-a { left: 716px; top: -4px; font-size: 162px; }
  .headline-girls { left: 556px; top: 124px; font-size: 190px; letter-spacing: -2px; }
  .headline-only { left: 568px; top: 268px; font-size: 172px; letter-spacing: -1px; }

  .program-title {
    left: 432px; top: 414px; font-size: 52px; line-height: 1; color: var(--white);
    letter-spacing: 0.5px; text-shadow: 2px 2px 2px rgba(0,0,0,0.55);
  }
  .program-note { left: 546px; top: 475px; font-size: 26px; line-height: 1; color: var(--ink); letter-spacing: 0.3px; }

  .founder {
    left: 324px; top: 543px; font-size: 47px; line-height: 1; color: var(--pink-soft);
    text-shadow: 1px 1px 1px rgba(60,20,80,0.35);
  }
  .brand-line {
    left: 438px; top: 601px; font-size: 54px; line-height: 1; color: var(--pink-soft);
    text-shadow: 2px 2px 2px rgba(40,10,60,0.6);
  }
  .tagline {
    font-family: "Kaushan Script", cursive;
    color: var(--white); font-size: 24px; line-height: 1;
  }
  .tagline-one { left: 330px; top: 690px; }
  .tagline-two { left: 456px; top: 731px; }

  .section-title { font-size: 27px; line-height: 1; color: var(--ink); }
  .offer-title { left: 118px; top: 798px; }
  .about-title { left: 572px; top: 790px; font-size: 26px; }

  .offer-list { position: absolute; left: 100px; top: 848px; margin: 0; padding: 0; list-style: none; }
  .offer-list li {
    position: relative; padding-left: 16px; font-size: 22px; line-height: 22px;
    margin-bottom: 5px; color: var(--ink);
  }
  .offer-list li::before {
    content: ""; position: absolute; left: 0; top: 6px; width: 5px; height: 5px;
    border: 1.5px solid var(--ink); border-radius: 50%;
  }
  .offer-list li.two-line { margin-bottom: 9px; }

  .about-text {
    position: absolute; left: 430px; top: 828px; width: 406px; margin: 0;
    font-size: 17px; line-height: 25.5px; font-style: italic; color: var(--ink);
  }
  .hours-intro {
    left: 474px; top: 974px; font-family: "Oswald", sans-serif; font-weight: 400;
    font-size: 16px; line-height: 1; color: var(--ink); letter-spacing: -0.2px;
  }
  .hours {
    left: 554px; top: 1008px; font-family: "Roboto", sans-serif; font-weight: 700;
    font-size: 16px; line-height: 1; color: var(--ink);
  }

  .contact-label { font-size: 21px; line-height: 1; color: var(--white); }
  .contact-value { color: var(--white); line-height: 1; }
  .address { left: 30px; top: 1128px; font-family: "Oswald", sans-serif; font-size: 15px; letter-spacing: -0.4px; }
  .address-note { left: 40px; top: 1150px; font-family: "Oswald", sans-serif; font-size: 7.5px; }
  .phone { left: 243px; top: 1125px; font-size: 25px; letter-spacing: -0.5px; }
  .email { left: 402px; top: 1134px; font-family: "Roboto", sans-serif; font-weight: 700; font-size: 10.5px; }
  .web { left: 606px; top: 1137px; font-family: "Roboto", sans-serif; font-weight: 700; font-size: 8px; }
</style>
</head>
<body>
<main class="flyer">
  <svg class="backdrop" width="861" height="1200" viewBox="0 0 861 1200">
    <defs>
      <linearGradient id="photoTone" x1="0" y1="0" x2="1" y2="1">
        <stop offset="0" stop-color="var(--photo-skin)"/>
        <stop offset="0.18" stop-color="var(--photo-light)"/>
        <stop offset="0.55" stop-color="var(--photo-mid)"/>
        <stop offset="1" stop-color="var(--photo-light)"/>
      </linearGradient>
    </defs>
    <rect x="0" y="0" width="861" height="1200" fill="url(#photoTone)" role="img" aria-label="Photograph of a girl in a white T-shirt"/>
    <polygon points="861,80 861,1200 0,1200 0,784" fill="var(--purple)"/>
    <polygon points="861,896 861,1200 680,1200" fill="var(--purple-light)"/>

    <g fill="none" stroke="var(--white)" stroke-width="2.5">
      <circle cx="57" cy="1096" r="17"/>
      <path d="M57 1106 C51 1099 49 1095 49 1091 a8 8 0 0 1 16 0 c0 4 -2 8 -8 15 z" stroke-width="2"/>
      <circle cx="57" cy="1091" r="2.6" stroke-width="1.8"/>

      <circle cx="238" cy="1101" r="17"/>
      <rect x="232" y="1090" width="12" height="21" rx="2.5" stroke-width="2"/>
      <line x1="236" y1="1107" x2="240" y2="1107" stroke-width="1.6"/>

      <circle cx="414" cy="1105" r="17"/>
      <rect x="405" y="1099" width="18" height="12" rx="1.5" stroke-width="2"/>
      <polyline points="405,1100 414,1106 423,1100" stroke-width="1.8"/>

      <circle cx="608" cy="1106" r="17"/>
    </g>
  </svg>

  <div class="logo-box">
    <div class="logo-name">Ridge Lass<br>Crew</div>
  </div>

  <h1 class="abs headline headline-a">A</h1>
  <p class="abs headline headline-girls">GIRLS</p>
  <p class="abs headline headline-only">ONLY</p>

  <h2 class="abs program-title">AFTER SCHOOL PROGRAM</h2>
  <p class="abs program-note">AS OSHC IS NO LONGER AVAILABLE</p>

  <p class="abs founder">THE BRAINCHILD OF REBECCA FOLWIN</p>
  <p class="abs brand-line">RIDGE LASS CREW</p>

  <p class="abs tagline tagline-one">Dedicated to Coaching &amp; Mentoring Our Girls</p>
  <p class="abs tagline tagline-two">into Strong, Independent Young women</p>

  <h3 class="abs section-title offer-title">WE OFFER</h3>
  <ul class="offer-list">
    <li>DAILY MEDITATION</li>
    <li>HEALTHY SNACKS</li>
    <li>DEDICATED HOMEWORK TIME</li>
    <li class="two-line">ORGANISED GROUP ACTIVITY,<br>(YOGA, FITNESS CLASS, SOCCER ETC.)</li>
    <li>REGULAR GUESTS SPEAKERS</li>
    <li>SOCIAL MEDIA FREE ZONE</li>
  </ul>

  <h3 class="abs section-title about-title">ABOUT US</h3>
  <p class="about-text">THE BRAINCHILD OF REBECCA FOLWIN, RIDGE LASS CREW WAS CREATED TO ADDRESS THE GROWING DEMAND FOR AFTER SCHOOL/SCHOOL HOLIDAY SUPERVISION FOR KIDS MOVING FROM PRIMARY INTO HIGH SCHOOL, WHEN OSHC CEASES TO EXIST.</p>

  <p class="abs hours-intro">OPEN EVERY AFTERNOON AND DURING SCHOOL HOLIDAYS</p>
  <p class="abs hours">3-6pm Monday to Friday</p>

  <p class="abs contact-label" style="left:79px;top:1087px;">ADDRESS</p>
  <p class="abs contact-value address">87 PELHAM PDE,&nbsp; BAULKHAM HILLS</p>
  <p class="abs contact-value address-note">(ACROSS FROM CRESTMOOR DAY CLINIC)</p>

  <p class="abs contact-label" style="left:269px;top:1095px;">PHONE</p>
  <p class="abs contact-value phone">0455817396</p>

  <p class="abs contact-label" style="left:448px;top:1096px;">EMAIL</p>
  <p class="abs contact-value email">info@ridgelasscrew.example.au</p>

  <p class="abs contact-label" style="left:642px;top:1097px;">FB PAGE</p>
  <p class="abs contact-value web">http://fb.example/ridgelasscrew</p>
</main>
</body>
</html>
```